Harbourline Physiotherapy business card design

We need a fresh, new business card design for our physiotherapy clinic Harbourline Physiotherapy

Will attach logo soon we had logo designed from our last project

Industry/Entity Type

Physical Therapy

Contact Information for Business Card

On front
Needs our logo, contact details:
58 Wexley Lane Kellridge NSW 2784
Ph/f: 02 9481 2057
info@harbourlinephysio.example.com.au

Requirements
Must have
• On the back of the card needs to have area to write down follow up appointments
• On front
• Needs our logo
• The colours have to be the colours in our logo which are: sky blue, black and white
• Font to be same as our logo please
• We want the card to look simple, not too cluttered but to the point
Should not have
• We don't need any extra pictures other than our logo

```html
<!DOCTYPE html>
<html lang="en">
<head>
<meta charset="utf-8">
<title>Harbourline Physiotherapy – Business Card</title>
<link rel="stylesheet" href="https://fonts.googleapis.com/css2?family=Source+Sans+3:ital,wght@0,400;0,600;1,400&display=swap">
<style>
  :root {
    --page-bg: #e9eaec;
    --card-white: #ffffff;
    --blue-deep: #2a2fa6;
    --blue-mid: #3a5fd0;
    --sky-blue: #2a9fe0;
    --ink: #2b2b2b;
    --line: #6a6a6a;
    --on-blue: #ffffff;
  }
  * { box-sizing: border-box; margin: 0; padding: 0; }
  html, body {
    width: 1200px; height: 950px; overflow: hidden;
    background: var(--page-bg);
    font-family: "Source Sans 3", "Myriad Pro", Arial, sans-serif;
  }
  .sheet {
    width: 1200px; height: 950px;
    display: flex; align-items: center; justify-content: center; gap: 40px;
  }
  .card {
    position: relative;
    width: 540px; height: 310px;
    background: var(--card-white);
    border-radius: 4px;
    box-shadow: 0 6px 18px rgba(0,0,0,.14);
    overflow: hidden;
  }

  /* Front */
  .front-band { position: absolute; inset: 0; width: 100%; height: 100%; }
  .holder { position: absolute; left: 30px; top: 40px; color: var(--on-blue); }
  .holder-name { font-size: 22px; font-weight: 600; letter-spacing: .2px; }
  .holder-role { font-size: 14px; margin-top: 2px; }
  .contacts { position: absolute; left: 30px; bottom: 26px; color: var(--on-blue); font-size: 13px; line-height: 1.45; }
  .address { margin-bottom: 10px; }
  .contact-row { display: flex; align-items: center; gap: 8px; }
  .contact-row svg { width: 11px; height: 11px; flex: none; }

  .brand { display: flex; align-items: center; gap: 10px; }
  .brand-dot { width: 14px; height: 14px; border-radius: 50%; background: var(--sky-blue); flex: none; }
  .brand-name { color: var(--sky-blue); font-weight: 600; font-size: 22px; line-height: 1.05; }
  .front .brand { position: absolute; right: 28px; top: 34px; }

  /* Back */
  .back .brand { position: absolute; left: 50%; top: 26px; transform: translateX(-50%); }
  .back .brand-name { font-size: 20px; white-space: nowrap; }
  .appointments { position: absolute; left: 34px; right: 34px; top: 100px; }
  .appt-row {
    display: flex; align-items: flex-end; gap: 8px;
    font-size: 14px; color: var(--ink); height: 40px;
  }
  .appt-row .rule { border-bottom: 1px solid var(--line); height: 1px; margin-bottom: 4px; }
  .rule-date { flex: 1.3; }
  .rule-time { flex: 1; }
  .notice {
    position: absolute; left: 0; right: 0; bottom: 22px; text-align: center;
    font-size: 12.5px; font-style: italic; color: var(--ink);
  }
</style>
</head>
<body>
<main class="sheet">

  <section class="card front" aria-label="Business card front">
    <svg class="front-band" viewBox="0 0 540 310" preserveAspectRatio="none" aria-hidden="true">
      <defs>
        <radialGradient id="bandGlow" cx="0.45" cy="0.5" r="0.7">
          <stop offset="0" stop-color="#4f8fe6"/>
          <stop offset="0.55" stop-color="#3459c8"/>
          <stop offset="1" stop-color="#2a2fa6"/>
        </radialGradient>
      </defs>
      <path d="M0 0 H300 C250 70 245 230 330 310 H0 Z" fill="url(#bandGlow)"/>
      <path d="M300 0 C250 70 245 230 330 310" fill="none" stroke="#8a8a8a" stroke-width="2"/>
      <path d="M318 0 C272 80 270 220 352 310" fill="none" stroke="#c4c4c4" stroke-width="1.2"/>
    </svg>

    <div class="holder">
      <p class="holder-name">Daniel Reeve</p>
      <p class="holder-role">CEO/Founder</p>
    </div>

    <div class="contacts">
      <p class="address">58 Wexley Lane Kellridge<br>NSW 2784</p>
      <p class="contact-row">
        <svg viewBox="0 0 12 12" aria-hidden="true"><path d="M2 1h2.5l1 3-1.5 1c.6 1.3 1.7 2.4 3 3l1-1.5 3 1V10c0 .6-.4 1-1 1C5 11 1 7 1 2c0-.6.4-1 1-1z" fill="#fff"/></svg>
        02 9481 2057
      </p>
      <p class="contact-row">
        <svg viewBox="0 0 12 12" aria-hidden="true"><rect x="3" y="1" width="6" height="3" fill="#fff"/><rect x="1" y="4.5" width="10" height="4.5" rx="1" fill="#fff"/><rect x="3" y="8" width="6" height="3" fill="#fff" stroke="#3459c8" stroke-width=".6"/></svg>
        02 9481 2057
      </p>
      <p class="contact-row">
        <svg viewBox="0 0 12 12" aria-hidden="true"><rect x="1" y="2.5" width="10" height="7" fill="#fff"/><path d="M1 2.5l5 4 5-4" fill="none" stroke="#3459c8" stroke-width=".9"/></svg>
        info@harbourlinephysio.example.com.au
      </p>
      <p class="contact-row">
        <svg viewBox="0 0 12 12" aria-hidden="true"><circle cx="6" cy="6" r="5" fill="#fff"/><path d="M1 6h10M6 1c-2 2.5-2 7.5 0 10M6 1c2 2.5 2 7.5 0 10" fill="none" stroke="#3459c8" stroke-width=".7"/></svg>
        www.harbourlinephysio.example.com.au
      </p>
    </div>

    <div class="brand">
      <span class="brand-dot" aria-hidden="true"></span>
      <span class="brand-name">Harbourline<br>Physiotherapy</span>
    </div>
  </section>

  <section class="card back" aria-label="Business card back, appointment reminder">
    <div class="brand">
      <span class="brand-dot" aria-hidden="true"></span>
      <span class="brand-name">Harbourline Physiotherapy</span>
    </div>

    <div class="appointments">
      <div class="appt-row"><span>Date</span><span class="rule rule-date"></span><span>Time</span><span class="rule rule-time"></span><span>am/pm</span></div>
      <div class="appt-row"><span>Date</span><span class="rule rule-date"></span><span>Time</span><span class="rule rule-time"></span><span>am/pm</span></div>
      <div class="appt-row"><span>Date</span><span class="rule rule-date"></span><span>Time</span><span class="rule rule-time"></span><span>am/pm</span></div>
    </div>

    <p class="notice">Please give 24 hours notice cancelling your appointment or a fee may be charged</p>
  </section>

</main>
</body>
</html>
```